wealth management firm, professional group, new model

we have a logo that works but we need a card, white background using our colors...clean look

our tag line if can be used in

The Bridge From Client to Owner

```html
<!DOCTYPE html>
<html lang="en">
<head>
<meta charset="utf-8">
<title>Arvel Wealth Partners – Business Card</title>
<link href="https://fonts.googleapis.com/css2?family=Open+Sans:wght@400;700&display=swap" rel="stylesheet">
<style>
  :root {
    --navy: #22365f;
    --ink: #3d3d3d;
    --muted: #555555;
    --paper: #ffffff;
    --backdrop: #e6e7ea;
    --rule: #7b7f88;
  }
  * { box-sizing: border-box; margin: 0; padding: 0; }
  html, body { width: 1200px; height: 900px; overflow: hidden; }
  body {
    background: var(--backdrop);
    font-family: "Open Sans", Arial, sans-serif;
    position: relative;
  }
  .card {
    position: absolute;
    left: 290px;
    width: 620px;
    height: 354px;
    background: var(--paper);
    border-radius: 16px;
    overflow: hidden;
    box-shadow: 0 6px 18px rgba(0,0,0,0.18);
  }
  .card--front { top: 58px; }
  .card--back { top: 470px; }

  .band {
    position: absolute;
    left: 0; right: 0;
    top: 258px;
    height: 48px;
    background: var(--navy);
    color: var(--paper);
    font-size: 22px;
    display: flex;
    align-items: center;
    justify-content: center;
    white-space: nowrap;
  }

  .brand-name {
    position: absolute;
    font-family: "Open Sans", Arial, sans-serif;
    font-weight: 400;
    color: var(--navy);
    white-space: nowrap;
    line-height: 1.2;
  }
  .card--front .brand-name {
    left: 0; right: 0; top: 110px;
    text-align: center;
    font-size: 40px;
  }
  .card--back .brand-name {
    left: 24px; width: 260px; top: 110px;
    text-align: center;
    font-size: 22px;
  }

  .divider {
    position: absolute;
    left: 298px; top: 50px;
    width: 1.5px; height: 150px;
    background: var(--rule);
  }
  .contact {
    position: absolute;
    left: 322px; top: 50px;
    color: var(--ink);
  }
  .contact__name {
    font-weight: 700; font-size: 26px; color: var(--navy);
    line-height: 1.15;
    white-space: nowrap;
  }
  .contact__role { font-size: 20px; color: var(--muted); margin-bottom: 8px; }
  .contact__list { list-style: none; }
  .contact__item {
    display: flex; align-items: center; gap: 8px;
    font-size: 20px; line-height: 1.4;
    white-space: nowrap;
  }
  .contact__item svg { width: 16px; height: 16px; fill: var(--ink); flex: none; }
</style>
</head>
<body>

<section class="card card--front" aria-label="Business card front">
  <p class="brand-name">Arvel Wealth Partners</p>
  <div class="band">The Bridge From Client to Owner</div>
</section>

<section class="card card--back" aria-label="Business card back">
  <p class="brand-name">Arvel Wealth Partners</p>
  <div class="divider"></div>
  <div class="contact">
    <p class="contact__name">DANIEL HARTLEY</p>
    <p class="contact__role">Managing Director</p>
    <ul class="contact__list">
      <li class="contact__item">
        <svg viewBox="0 0 16 16" aria-hidden="true"><path d="M2 5c0-2 2-3 6-3s6 1 6 3v1h-3V4.8C10 4.3 9 4 8 4s-2 .3-3 .8V6H2zM4 8l2-2h4l2 2v5H4zm4 1.2a1.6 1.6 0 100 3.2 1.6 1.6 0 000-3.2z"/></svg>
        044-987 654 321
      </li>
      <li class="contact__item">
        <svg viewBox="0 0 16 16" aria-hidden="true"><path d="M1 4h14v9H1zm1.5 1.2v.4L8 9.3l5.5-3.7v-.4zM2.5 7.4v4.4h11V7.4L8 11z"/></svg>
        info@arvelwp.com
      </li>
      <li class="contact__item">
        <svg viewBox="0 0 16 16" aria-hidden="true"><path d="M8 1a7 7 0 100 14A7 7 0 008 1zm-1 2.2c-.5.8-1.7 1-1.6 2 .1.9 1.4.6 1.8 1.4.4.8-.7 1.5-.2 2.4.5.8 1.6.4 1.8 1.4.1.8-.5 1.6-.2 2.4A5.2 5.2 0 013 8a5 5 0 014-4.8zm3 .6A5 5 0 0113 8c-.5-.3-1-.3-1.5 0-.6.4-1.3 0-1.3-.8 0-.9-1-1-1-1.9 0-.6.5-1 .8-1.5z"/></svg>
        www.arvelwp.com
      </li>
    </ul>
  </div>
  <div class="band">Your Address, City, State, Zip 0000</div>
</section>

</body>
</html>
```